Profesional personal website needs design and business card

I need a business card with my professional name as a logo "Dorian Vitality" for my business. I am a Wellness Coach, consultant and trainer. So it should be professional, wellness oriented and modern.

Target Market(s)

Private clients, governments, corporations. Luxury and high market.

Industry/Entity Type

Health And Wellness

Contact Information for Business Card

Dorian Vitality should be the logo

Colors

Designer to choose colors to be used in the design.

Requirements
Must have
• Dorian Vitality
• Name: Tomás Lirandel
• Wellness Coach, Consultant & Trainer.
• Website: www.dorianvitality-example.com
• Phone:
• Spain (+34) 612 480 317
• (USA) +1 (555) 610 4829
Nice to have
• The most important is the design of "Dorian Vitality", as this is going to be my personal brand logo. It should be professional, wellness, high end and actual.
Should not have
• no golds, no baroque style..

```html
<!DOCTYPE html>
<html lang="en">
<head>
<meta charset="UTF-8">
<title>Dorian Vitality — Business Card</title>
<link href="https://fonts.googleapis.com/css2?family=Lato:wght@400;700&display=swap" rel="stylesheet">
<style>
  :root {
    --brand-blue: #02729a;
    --ink: #3d4450;
    --ink-dark: #23272e;
    --paper: #ffffff;
    --backdrop: #ffffff;
    --shadow: rgba(0, 0, 0, 0.28);
  }
  * { margin: 0; padding: 0; box-sizing: border-box; }
  html, body {
    width: 1200px; height: 1200px; overflow: hidden;
    background: var(--backdrop);
    font-family: "Lato", Arial, sans-serif;
  }
  .canvas { position: relative; width: 1200px; height: 1200px; }
  .card {
    position: absolute; left: 180px; width: 840px;
    box-shadow: 4px 5px 6px var(--shadow);
  }
  .card--front { top: 84px; height: 476px; background: var(--paper); }
  .card--back { top: 640px; height: 478px; background: var(--brand-blue); }

  .wordmark {
    position: absolute;
    font-weight: 700; text-transform: uppercase;
    line-height: 1; text-align: center;
  }
  .card--front .wordmark {
    left: 96px; top: 190px; width: 288px;
    color: var(--brand-blue); font-size: 46px; letter-spacing: 4px;
  }
  .card--back .wordmark {
    left: 228px; top: 178px; width: 384px;
    color: var(--paper); font-size: 66px; letter-spacing: 6px;
  }
  .wordmark span { display: block; }
  .wordmark span + span { margin-top: 10px; }

  .divider {
    position: absolute; left: 420px; top: 154px;
    width: 3px; height: 164px; background: var(--brand-blue);
  }
  .details { position: absolute; left: 460px; top: 170px; }
  .details__name {
    font-size: 38px; font-weight: 700; color: var(--brand-blue);
    line-height: 1; letter-spacing: -0.3px;
  }
  .details__role {
    margin-top: 6px; font-size: 19.5px; color: var(--ink); line-height: 1;
  }
  .contact { list-style: none; margin-top: 20px; }
  .contact li {
    display: flex; align-items: center; gap: 8px;
    font-size: 19.5px; color: var(--ink-dark); line-height: 1; height: 29.5px;
  }
  .contact svg { width: 19px; height: 19px; flex: none; fill: var(--brand-blue); }
  .contact .region { color: var(--brand-blue); }

  .back-url {
    position: absolute; left: 0; right: 0; top: 426px;
    text-align: center; color: var(--paper); font-size: 19.5px;
  }
</style>
</head>
<body>
<div class="canvas">
  <section class="card card--front">
    <div class="wordmark"><span>Dorian</span><span>Vitality</span></div>
    <div class="divider"></div>
    <div class="details">
      <h1 class="details__name">Tomás Lirandel</h1>
      <p class="details__role">Wellness Coach, Consultant &amp; Trainer</p>
      <ul class="contact">
        <li>
          <svg viewBox="0 0 24 24" aria-hidden="true"><path d="M6.6 10.8c1.4 2.8 3.8 5.1 6.6 6.6l2.2-2.2c.3-.3.7-.4 1-.2 1.1.4 2.3.6 3.6.6.6 0 1 .4 1 1V20c0 .6-.4 1-1 1C10.6 21 3 13.4 3 4c0-.6.4-1 1-1h3.5c.6 0 1 .4 1 1 0 1.3.2 2.5.6 3.6.1.3 0 .7-.2 1L6.6 10.8z"/></svg>
          <span>(+34) 612 480 317 <span class="region">Spain</span></span>
        </li>
        <li>
          <svg viewBox="0 0 24 24" aria-hidden="true"><path d="M8 2h8a2 2 0 0 1 2 2v16a2 2 0 0 1-2 2H8a2 2 0 0 1-2-2V4a2 2 0 0 1 2-2zm0 3v12h8V5H8zm4 13.5a1 1 0 1 0 0 2 1 1 0 0 0 0-2z"/></svg>
          <span>+1 (555) 610 4829 <span class="region">(USA)</span></span>
        </li>
        <li>
          <svg viewBox="0 0 24 24" aria-hidden="true"><path d="M12 2a10 10 0 1 0 0 20 10 10 0 0 0 0-20zm6.9 6h-2.9a15.7 15.7 0 0 0-1.4-3.6A8 8 0 0 1 18.9 8zM12 4c.8 1.2 1.5 2.5 1.9 4h-3.8c.4-1.5 1.1-2.8 1.9-4zM4.3 14a8 8 0 0 1 0-4h3.4a16.5 16.5 0 0 0 0 4H4.3zm.8 2h2.9c.3 1.3.8 2.5 1.4 3.6A8 8 0 0 1 5.1 16zM8 8H5.1a8 8 0 0 1 4.3-3.6C8.8 5.5 8.3 6.7 8 8zm4 12c-.8-1.2-1.5-2.5-1.9-4h3.8c-.4 1.5-1.1 2.8-1.9 4zm2.3-6H9.7a14.7 14.7 0 0 1 0-4h4.6a14.7 14.7 0 0 1 0 4zm.3 5.6c.6-1.1 1.1-2.3 1.4-3.6h2.9a8 8 0 0 1-4.3 3.6zm1.7-5.6a16.5 16.5 0 0 0 0-4h3.4a8 8 0 0 1 0 4h-3.4z"/></svg>
          <span>www.dorianvitality-example.com</span>
        </li>
      </ul>
    </div>
  </section>

  <section class="card card--back">
    <div class="wordmark"><span>Dorian</span><span>Vitality</span></div>
    <p class="back-url">www.dorianvitality-example.com</p>
  </section>
</div>
</body>
</html>
```